Re-design an HTML Website

Website must be responsive/fluid and designed with mobile-first priority. I want to be able to make changes with a HTML editor

We offer EMF Protection devices that neutralize EMF radiations emitted from electronics. We have devices for people and cell phones.
.

Redesign our Website (www.brightpebs.us) to look more modern, but I need to keep it in an HTML format. I plan on keeping the same shopping cart service (CraftLedger.com), as it has some features we need, but it is BUTTON intensive.

Requirements requested (samples submitted):
Headers and Footers
Menu setup as submitted
Creative Landing Page
Categories Page (must be stacked products)
Products Page (must be stacked products)
Individual Product Page
Generic 1-Column Page
Generic 2-Column Page
Generic 3-Column Page
Updates

What we sell are devices to neutralize the electromagnetic radiation (EMF) emitted from cell phones and electronics. Anything thing you can do to bring this website (www.BrightPEBs.us) into the 21st Century will be appreciated. It is a secondary website for our Affiliate Accounts - our primary site is at Vendaro www.PrimeEMFGoods.com

Be creative -- make us look and feel great!

Thanks, Oliver

Providing both a Mobile & Desktop screen shot would be helpful.

Also, do not use the products from pulsewafers.com - it is a slightly different product.
www.PrimeEMFGoods.com or www.BrightPEBs.us are our product configurations.

Industry/Entity Type

Technologoy

Coding

Coded - Design and coding required

Number of Pages Required

5+ page

Requirements
Must have
• Zip file and desciptions included
Nice to have
• Menu / footer /header / Landing page / Product Page / Category Page

```html
<!DOCTYPE html>
<html lang="en">
<head>
<meta charset="utf-8">
<title>Bright Pebs – EMF Protection Devices</title>
<link rel="stylesheet" href="https://fonts.googleapis.com/css2?family=Inter:wght@400;500;600;700;800&display=swap">
<style>
:root{
  --blue:#1f5a93;
  --navy:#0d2a52;
  --navy-box:#163a6b;
  --yellow:#ffff00;
  --ink:#2a2a2a;
  --text:#555;
  --line:#d9d9d9;
  --white:#fff;
}
*{box-sizing:border-box;margin:0;padding:0}
html,body{width:1200px;height:3391px;overflow:hidden}
body{font-family:"Inter",Arial,sans-serif;color:var(--ink);background:var(--white);position:relative}
a{color:inherit;text-decoration:none}

.promo-bar{position:absolute;top:0;left:0;width:1200px;height:42px;background:var(--blue);color:var(--white);font-size:15px;display:flex;align-items:center;justify-content:center}

.hero{position:absolute;top:42px;left:0;width:1200px;height:646px;overflow:hidden}
.hero-photo{position:absolute;inset:0;background:linear-gradient(100deg,#3c4347 0%,#6d7275 30%,#8e8f8d 55%,#4a4e50 80%,#2f3336 100%)}
.hero-shade{position:absolute;left:0;right:0;bottom:0;height:260px;background:linear-gradient(180deg,rgba(10,30,60,0),rgba(10,30,60,.55))}
.site-nav{position:absolute;top:0;left:0;width:1200px;height:82px;background:rgba(50,50,50,.72);display:flex;align-items:center}
.brand{position:absolute;left:110px;top:22px;color:var(--white);font-size:30px;font-weight:700}
.nav-links{position:absolute;left:328px;top:0;display:flex;height:82px;align-items:center;font-size:14px;font-weight:500;color:var(--white)}
.nav-links a{margin-right:33px}
.nav-links .active{position:relative;width:66px;height:96px;margin-right:20px;display:flex;align-items:center;justify-content:center;color:#333;align-self:flex-start;padding-bottom:14px}
.nav-links .active svg{position:absolute;inset:0}
.nav-links .active span{position:relative}
.hero-title{position:absolute;left:0;width:1200px;top:488px;text-align:center;color:var(--white);font-size:92px;font-weight:800;letter-spacing:1px}
.hero-arrow{position:absolute;top:514px;width:48px;height:48px;border-radius:50%;background:rgba(255,255,255,.45);display:flex;align-items:center;justify-content:center}

.products-title{position:absolute;top:766px;width:1200px;text-align:center;font-size:41px;font-weight:800}
.tab{position:absolute;top:838px;width:233px;height:41px;border-radius:21px;background:var(--blue);color:var(--white);font-size:15px;font-weight:700;display:flex;align-items:center;justify-content:center}
.tab.current{background:var(--yellow);color:#333}
.tab-pointer{position:absolute;top:880px;left:593px}

.product-card{position:absolute;width:479px;height:360px;border:1px solid var(--line);background:var(--white)}
.product-art{position:absolute;left:36px;top:24px;width:130px;height:290px;background:linear-gradient(180deg,#f4f4f4,#e6e6ea);border-radius:4px}
.product-info{position:absolute;left:202px;top:30px;width:250px}
.product-type{color:var(--blue);font-size:15px;font-weight:700}
.product-pack{font-size:15px;font-weight:600;margin-top:12px}
.product-price{color:var(--blue);font-size:23px;font-weight:700;margin-top:8px}
.product-desc{font-size:14px;line-height:21px;color:var(--text);margin-top:13px}
.product-desc + .product-desc{margin-top:21px}
.view-btn{position:absolute;left:202px;top:283px;width:234px;height:41px;border:2px solid var(--blue);border-radius:21px;color:var(--blue);font-size:15px;font-weight:700;display:flex;align-items:center;justify-content:center}

.consult{position:absolute;top:1771px;left:0;width:1200px;height:648px;background:var(--blue);overflow:hidden}
.consult-accent{position:absolute;inset:0}
.consult-photo{position:absolute;left:698px;top:95px;width:296px;height:440px;border-radius:140px 140px 0 0;background:linear-gradient(180deg,#7a5a48 0%,#c9a38c 30%,#3d8a8d 55%,#2f7478 100%)}
.consult-copy{position:absolute;left:109px;top:74px;width:443px;color:var(--white)}
.consult-copy h2{font-size:38px;line-height:47px;font-weight:800}
.consult-copy .byline{font-size:14px;font-weight:700;margin-top:12px}
.consult-copy p{font-size:14.5px;line-height:21px;text-align:justify;margin-top:22px}
.consult-copy .byline + p{margin-top:23px}
.consult-copy .sub{font-size:14px;font-weight:700;margin-top:15px}
.consult-btn{display:inline-flex;width:234px;height:41px;border-radius:21px;background:var(--yellow);color:#222;font-size:15px;font-weight:700;align-items:center;justify-content:center;margin-top:20px}
.name-plate{position:absolute;left:632px;top:535px;width:568px;height:113px;background:var(--navy);color:var(--white);font-size:21px;font-weight:700;display:flex;align-items:center;justify-content:center}

.commitment{position:absolute;top:2505px;left:0;width:1200px;text-align:center}
.commitment h2{font-size:40px;font-weight:800}
.commitment h3{color:var(--blue);font-size:26px;font-weight:700;margin-top:16px}
.commitment p{width:890px;margin:24px auto 0;font-size:14px;line-height:21.5px;color:var(--text)}
.commitment p + p{margin-top:21px}
.mail-btn{display:inline-flex;margin-top:30px;width:234px;height:40px;border-radius:20px;background:var(--blue);color:var(--white);font-size:13px;font-weight:700;align-items:center;justify-content:center}

.site-footer{position:absolute;top:2957px;left:0;width:1200px;height:434px;background:var(--navy);color:var(--white)}
.footer-strip{position:absolute;left:395px;top:66px;width:405px;height:24px;background:var(--yellow);color:#333;font-size:14.5px;display:flex;align-items:center;justify-content:center;gap:30px}
.contact-box{position:absolute;top:118px;width:308px;height:145px;background:var(--navy-box);text-align:center;display:flex;flex-direction:column;justify-content:center}
.contact-box .label{font-size:14px;text-transform:uppercase}
.contact-box .value{font-weight:700;font-size:18px;margin-top:8px;line-height:22px}
.contact-box .value.big{font-size:22px}
.footer-rule{position:absolute;left:110px;top:294px;width:980px;height:1px;background:rgba(255,255,255,.6)}
.footer-links{position:absolute;top:330px;left:0;width:1200px;display:flex;justify-content:center;gap:82px;font-size:14.5px}
.copyright{position:absolute;top:382px;width:1200px;text-align:center;font-size:14.5px}
</style>
</head>
<body>

<div class="promo-bar">Free Shipping Over $299</div>

<header class="hero">
  <div class="hero-photo" role="img" aria-label="Photo of two smiling colleagues looking at a laptop with colourful EMF stickers in a bright office"></div>
  <div class="hero-shade"></div>
  <nav class="site-nav">
    <a class="brand" href="#">Bright Pebs</a>
    <div class="nav-links">
      <a class="active" href="#">
        <svg width="66" height="96" viewBox="0 0 66 96"><polygon points="0,0 66,0 66,82 33,96 0,82" fill="#ffff00"/></svg>
        <span>Home</span>
      </a>
      <a href="#">EMF Protection Devices</a>
      <a href="#">Savings Options</a>
      <a href="#">Why these Products / &nbsp;Recommendations</a>
      <a href="#">More &#8964;</a>
    </div>
  </nav>
  <div class="hero-arrow" style="left:63px">
    <svg width="14" height="14" viewBox="0 0 14 14"><path d="M9 2 L4 7 L9 12" stroke="#fff" stroke-width="1.6" fill="none"/></svg>
  </div>
  <div class="hero-arrow" style="left:1088px">
    <svg width="14" height="14" viewBox="0 0 14 14"><path d="M5 2 L10 7 L5 12" stroke="#fff" stroke-width="1.6" fill="none"/></svg>
  </div>
  <h1 class="hero-title">BRIGHT PEBS</h1>
</header>

<h2 class="products-title">EMF PROTECTION PRODUCTS</h2>
<a class="tab" href="#" style="left:243px">FOR ALL ELECTRONICS</a>
<a class="tab current" href="#" style="left:484px">FOR YOU</a>
<a class="tab" href="#" style="left:724px">FOR THE HOME</a>
<svg class="tab-pointer" width="14" height="14" viewBox="0 0 14 14"><polygon points="0,0 14,0 7,13" fill="#1f5a93"/></svg>

<article class="product-card" style="left:110px;top:917px">
  <div class="product-art" role="img" aria-label="Starter package illustration: tag pendants in white or black on a cord, plus a phone with dots"></div>
  <div class="product-info">
    <div class="product-type">TAG</div>
    <div class="product-pack">STARTER PACKAGE</div>
    <div class="product-price">$69.95</div>
    <p class="product-desc">Includes the Body/Bio PEB embedded in the TAG for you to wear or keep near you to strengthen and balance your energy field.</p>
    <p class="product-desc">Plus 1 Bright PEB Set– For your cell phone Personal wearable technology!</p>
  </div>
  <a class="view-btn" href="#">VIEW DETAILS</a>
</article>

<article class="product-card" style="left:611px;top:917px">
  <div class="product-art" role="img" aria-label="Starter package illustration: clip pendants in white or black, plus a phone with dots"></div>
  <div class="product-info">
    <div class="product-type">CLIP</div>
    <div class="product-pack">STARTER PACKAGE</div>
    <div class="product-price">$69.95</div>
    <p class="product-desc">Includes the Body/Bio PEB embedded in the CLIP for you to wear or keep near you to strengthen and balance your energy field.</p>
    <p class="product-desc">Plus 1 Bright PEB Set – For your cell phone</p>
  </div>
  <a class="view-btn" href="#">VIEW DETAILS</a>
</article>

<article class="product-card" style="left:110px;top:1303px">
  <div class="product-art" role="img" aria-label="Starter package illustration: wristbands in white or black, plus a phone with dots"></div>
  <div class="product-info">
    <div class="product-type">WRISTBAND</div>
    <div class="product-pack">STARTER PACKAGE</div>
    <div class="product-price">$69.95</div>
    <p class="product-desc">Includes the Body/Bio PEB embedded in the wristBAND for you to wear or keep near you to strengthen and balance your energy field.</p>
    <p class="product-desc">Plus 1 Bright PEB Set – For your cell phone</p>
  </div>
  <a class="view-btn" href="#">VIEW DETAILS</a>
</article>

<article class="product-card" style="left:611px;top:1303px">
  <div class="product-art" role="img" aria-label="Starter package illustration: three colourful adhesive dots, plus a phone with dots"></div>
  <div class="product-info">
    <div class="product-type">BODY/BIO PEB</div>
    <div class="product-pack">STARTER PACKAGE</div>
    <div class="product-price">$69.95</div>
    <p class="product-desc">Includes the Body/Bio PEB &nbsp;adhesive PEB, which can be adhered to a watch or favorite piece of jewelry (or carry in a pocket). Optional use: place on cell with Bright PEB to receive the wearable benefits.</p>
  </div>
  <a class="view-btn" href="#">VIEW DETAILS</a>
</article>

<section class="consult">
  <svg class="consult-accent" width="1200" height="648" viewBox="0 0 1200 648"><polygon points="955,0 1200,0 1200,535 685,535" fill="#ffff00"/></svg>
  <div class="consult-photo" role="img" aria-label="Portrait of the health consultant in a teal jacket"></div>
  <div class="consult-copy">
    <h2>EDUCATIONAL HEALTH CONSULTATION</h2>
    <div class="byline">WITH HELENA MARWICK, CLS, NCMP, PH.D.</div>
    <p>Clinical Laboratory Scientist – Midlife Health Soc. Certified Menopause Practitioner – Medical Researcher – Author</p>
    <p>Also specializing in electromagnetic fields (EMF) symptoms resolution. Understanding what you are going through and how to get help can be a difficult and tedious process.</p>
    <p>Dr. Marwick's 25 years of experience allows her to quickly assess what works and what does not. Her goal is to get you on the right track so that you can obtain the health care that is best for you and your family.</p>
    <div class="sub">ELECTROMAGNETIC SENSITIVITY CONSULTATIONS</div>
    <a class="consult-btn" href="#">CONSULTATION</a>
  </div>
  <div class="name-plate">HELENA MARWICK, CLS, NCMP, PH.D.</div>
</section>

<section class="commitment">
  <h2>OUR COMMITMENT</h2>
  <h3>"OFFER THE BEST AVAILABLE EMF PRODUCTS!"</h3>
  <p>As researchers, we will continue to search for the most effective EMF products and make them available to you and your families. &nbsp;We encourage families to cover the environments and devices they can control-and you will do better than your neighbors. &nbsp;Most are choosing to ignore or discount the scientific evidence proving the harm EMF creates.</p>
  <p>Please contact us with any questions, as this product line is a little complicated &nbsp;and well worth the time investment to ensure you obtain the best coverage possible. &nbsp;We utilize customized Bright PEB Sets to offset the extreme EMF exposures we are subjected to here in the USA-EMF exposures are not going to go away, and we all need to cover as many electronic devices as possible.</p>
  <a class="mail-btn" href="#">oliver@brightPEBs.us</a>
</section>

<footer class="site-footer">
  <div class="footer-strip"><span>FREE SHIPPING OVER $299</span><span>/</span><span>180-DAY RETURNS</span></div>
  <div class="contact-box" style="left:110px">
    <div class="label">Phone :</div>
    <div class="value big">949 555-0186</div>
  </div>
  <div class="contact-box" style="left:447px">
    <div class="label">Email :</div>
    <div class="value">Info@PrimeEMFGoods.com</div>
  </div>
  <div class="contact-box" style="left:783px">
    <div class="label">Address :</div>
    <div class="value">Irvine, CA USA Meridian<br>Wellness Consulting LLC</div>
  </div>
  <div class="footer-rule"></div>
  <div class="footer-links">
    <a href="#">PRIVACY POLICY</a>
    <a href="#">RETURNS POLICY</a>
    <a href="#">CONTACT</a>
  </div>
  <div class="copyright">© 2024 Copyrights | All Rights Reserved</div>
</footer>

</body>
</html>
```